Music Producer Website

I need a website designed for my music production company. We specialize in finding talented musicians and matching them with music producers all over the United States. A visitor can create a profile and/or upload their music demo and we submit it to thousands of music producers and production companies for review. In many cases, our members will receive multiple signing offers from music producers allowing them to choose the contract that is best for them. "We turn aspiring musicians into SuperStars!"
Please include photos that reflect all genres of music (black artists, white artists, both male and female.) We produce all types of music including rap, R&B, rock, country, and Hip Hop.
When a user creates a profile, they become visible to thousands of record producers who are looking to sign new talent and make them stars.
Somewhere in the top half of the page, please include a small form that the visitor can fill out. The form should look as follows:
Title (large and bold): Contact Us or Submit Music Demo
Fields to include (* = required): First Name*, Last Name*, Age, Zip Code, Email Address*, Daytime Phone, Evening Phone, Comments
Then, there will be a "submit" button to proceed to next step of form. Just below the "submit" button, should be the following verbiage: "After submitting, you will have the opportunity to upload demos of your music (optional) and provide other pertinent information about yourself, band, or group."
Updates
Reason: I have not seen a design that I am 100% satisfied with yet. Ideally, rotating header images (GIF or other) with several different music producers in studio (male, female, black, white) would be perfect. Here are some examples of how the header pics could look:
http://files.quillmarsh.net/art_img/514302/806421/806421_7391046_514302_image.jpg
http://files.quillmarsh.net/art_img/514302/806421/806421_7391058_514302_image.jpg
http://files.quillmarsh.net/art_img/514302/806421/806421_7391037_514302_image.jpg
Also, there should be a form on the site (somewhere in upper half of the page) with the following headline:
GET FOUND AND BECOME A STAR! (super large, super-bold font)
Contact Us or Submit Your Music for Review (large font, not as bold as headline)
First Name
Last Name
Age
Zip Code
Email Address
Daytime Phone
Evening Phone
Comments
Target Market(s)
We are targeting all types of musicians including rock, rap, pop, R&B, country, gospel, etc.
Industry/Entity Type
Artists
Colors
Designer to choose colors to be used in the design.
Look and feel
Each slider illustrates characteristics of the customer's brand and the style your logo design should communicate.

```html
<!DOCTYPE html>
<html lang="en">
<head>
<meta charset="utf-8">
<title>Vireo Music Productions</title>
<link href="https://fonts.googleapis.com/css2?family=Lato:wght@300;400;700;900&display=swap" rel="stylesheet">
<style>
:root{
  --black:#000;
  --panel:#0b0a08;
  --gold:#b3a77f;
  --white:#fff;
  --muted:#8d8672;
  --field:#fff;
  --field-text:#a7a7a7;
  --cream:#e9e2d8;
  --red:#c8412a;
  --rule:#3a3629;
}
*{box-sizing:border-box;margin:0;padding:0}
html,body{width:1200px;height:2261px;overflow:hidden;background:var(--black)}
body{position:relative;font-family:'Lato',sans-serif;color:var(--white)}
.abs{position:absolute}

/* hero slider */
.hero-photo{left:0;top:0;width:1200px;height:693px;
  background:
    radial-gradient(ellipse 260px 240px at 300px 330px,rgba(232,225,210,.55),rgba(232,225,210,0) 70%),
    radial-gradient(ellipse 180px 150px at 330px 210px,rgba(170,130,95,.6),rgba(170,130,95,0) 75%),
    radial-gradient(ellipse 700px 160px at 600px 500px,rgba(214,190,70,.55),rgba(214,190,70,0) 70%),
    radial-gradient(ellipse at 75% 25%,#7a6a58 0%,#4a3e31 45%,#211b14 85%),
    #1a150f}
.hero-fade{left:0;top:560px;width:1200px;height:133px;background:linear-gradient(180deg,rgba(0,0,0,0),rgba(0,0,0,.85))}
.slider-arrow{top:278px;width:28px;height:28px}
.slider-arrow.prev{left:32px}.slider-arrow.next{left:1134px}

.site-header{left:119px;top:0;width:957px;height:122px;background:rgba(10,9,7,.95)}
.brand{left:34px;top:36px;color:var(--gold);font-weight:700;line-height:1}
.brand .name{font-size:38px;letter-spacing:2px;display:block}
.brand .sub{font-size:12px;letter-spacing:1px;display:block;margin-top:4px}
.account{left:655px;top:26px;font-size:15px}
.social{top:22px;width:26px;height:26px;border-radius:50%;background:#5a564b}
.search{left:914px;top:21px;width:28px;height:28px;border-radius:50%;background:var(--gold)}
.main-nav{left:386px;top:82px;display:flex;font-size:16px;font-weight:700}
.main-nav a{color:var(--white);text-decoration:none;position:relative;white-space:nowrap}
.main-nav a span{color:var(--gold)}
.main-nav a.active::before{content:"";position:absolute;left:0;top:-12px;width:97px;height:3px;background:var(--gold)}

.tagline-small{left:678px;top:334px;height:42px;width:392px;background:#ece7dc;color:#111;font-size:26px;font-weight:700;line-height:42px;text-align:center}
.tagline-big{left:678px;top:380px;width:398px;height:83px;background:rgba(0,0,0,.75);font-size:70px;font-weight:700;line-height:83px;text-align:right;padding-right:12px}

/* signup form */
.signup-bg{left:0;top:693px;width:1200px;height:253px;background:var(--black)}
.signup{left:75px;top:537px;width:1063px;height:405px;background:var(--panel)}
.signup h2{position:absolute;left:46px;top:22px;font-weight:900;line-height:1;text-transform:uppercase}
.signup h2 .l1{display:block;font-size:38px}
.signup h2 .l2{display:block;font-size:73px;color:var(--gold);margin-top:0}
.field{position:absolute;background:var(--field);color:var(--field-text);font-size:15px;padding:5px 10px}
.req{position:absolute;font-size:12px}
.artist-photo{left:697px;top:28px;width:306px;height:270px;
  background:radial-gradient(ellipse 110px 130px at 62% 42%,#b8b8b8,#6c6c6c 55%,rgba(40,40,40,0) 100%),
             radial-gradient(ellipse at 70% 90%,#5a5a5a,#1a1a1a 70%),#0b0a08}
.submit{left:697px;top:299px;width:306px;height:44px;background:var(--gold);font-size:32px;font-weight:700;text-align:center;line-height:44px;text-transform:uppercase}
.form-note{left:0;top:895px;width:1200px;text-align:center;font-size:13px;color:var(--muted)}

/* welcome */
.welcome{left:0;top:946px;width:1200px;height:373px;
  background:radial-gradient(ellipse 260px 300px at 700px 260px,rgba(35,28,20,.9),rgba(35,28,20,0) 70%),
             radial-gradient(ellipse at 62% 30%,#7a6346 0%,#3f3224 40%,#120e0a 85%)}
.welcome h1{position:absolute;left:160px;top:88px;font-size:74px;font-weight:700;line-height:1.1}
.welcome h1 span{display:block;color:var(--gold)}
.welcome .copy{position:absolute;left:529px;top:64px;width:552px;font-size:13px;line-height:17.5px;color:#eee}
.welcome .copy p+p{margin-top:17px}

/* testimonial */
.quote-rule{left:122px;top:1408px;width:956px;height:2px;background:var(--rule)}
.quote-badge{left:558px;top:1366px;width:84px;height:84px;border-radius:50%;border:2px solid var(--rule);background:var(--black);border-bottom-color:transparent}
.quote-mark{left:558px;top:1372px;width:84px;text-align:center;font-size:64px;font-weight:900;color:var(--gold);line-height:70px}
.quote-text{left:175px;top:1453px;width:850px;text-align:center;font-size:23px;font-weight:300;color:var(--gold);line-height:29px}
.quote-author{left:0;top:1547px;width:1200px;text-align:center;font-size:15px;font-weight:700}
.quote-author span{color:var(--gold);margin-left:8px}
.dot{width:10px;height:10px;border-radius:50%;background:var(--gold)}
.dot.on{background:var(--red)}

/* concerts */
.cream-strip{left:0;top:1620px;width:119px;height:468px;background:var(--cream)}
.schedule{left:119px;top:1620px;width:388px;height:468px;background:var(--black)}
.schedule h2{position:absolute;left:0;top:6px;width:388px;text-align:center;font-weight:700;line-height:1}
.schedule h2 .l1{display:block;font-size:64px}
.schedule h2 .l2{display:block;font-size:58px;color:var(--gold);margin-top:-4px}
.next-bar{left:0;top:142px;width:388px;height:58px;background:var(--gold);font-size:26px;font-weight:700;line-height:58px;padding-left:28px;text-transform:uppercase}
.cal-icon{left:330px;top:154px}
.gig{left:32px;width:330px}
.gig .date{font-size:16px;font-weight:700}
.gig .venue{font-size:19px;font-weight:700;color:var(--gold);line-height:28px;margin-top:12px}
.gig-rule{left:0;width:375px;height:1px;background:var(--rule)}
.map{left:507px;top:1620px;width:693px;height:468px;
  background:radial-gradient(ellipse 220px 130px at 45% 42%,#eee8de,rgba(238,232,222,0) 80%),
             radial-gradient(ellipse at 50% 55%,#d9c6ab 0%,#b9996f 60%,#a27f57 100%)}
.map-pin{width:44px;height:48px;background:#222;font-size:11px;font-weight:700;text-align:center;line-height:14px;padding-top:4px;border:1px solid #777}

/* footer */
.site-footer{left:0;top:2088px;width:1200px;height:173px;background:var(--black);text-align:center}
.footer-brand{left:0;top:46px;width:1200px;color:var(--gold);font-weight:700;line-height:1}
.footer-brand .name{font-size:34px;letter-spacing:2px;display:block}
.footer-brand .sub{font-size:11px;letter-spacing:1px;display:block;margin-top:3px}
.copyright{left:0;top:110px;width:1200px;font-size:12px}
.footer-links{left:0;top:136px;width:1200px;font-size:12px}
.footer-links a{color:var(--white);text-decoration:none}
</style>
</head>
<body>

<div class="abs hero-photo" role="img" aria-label="Slider photo: a producer wearing studio headphones in front of a cheering concert crowd with warm stage lights"></div>
<div class="abs hero-fade"></div>
<svg class="abs slider-arrow prev" viewBox="0 0 28 28"><path d="M18 4 L8 14 L18 24" fill="none" stroke="#fff" stroke-width="4"/></svg>
<svg class="abs slider-arrow next" viewBox="0 0 28 28"><path d="M10 4 L20 14 L10 24" fill="none" stroke="#fff" stroke-width="4"/></svg>

<header class="abs site-header">
  <div class="abs brand"><span class="name">VIREO</span><span class="sub">Music Productions</span></div>
  <div class="abs account">login / register</div>
  <div class="abs social" style="left:802px"></div>
  <div class="abs social" style="left:836px"></div>
  <div class="abs social" style="left:870px"></div>
  <div class="abs search">
    <svg width="28" height="28" viewBox="0 0 28 28"><circle cx="12.5" cy="12.5" r="5" fill="none" stroke="#fff" stroke-width="2"/><path d="M16 16 L20 20" stroke="#fff" stroke-width="2.5"/></svg>
  </div>
  <nav class="abs main-nav">
    <a class="active" href="#" style="width:152px">About <span>Vireo</span></a>
    <a href="#" style="width:146px">Team <span>Vireo</span></a>
    <a href="#" style="width:130px">Join <span>Vireo</span></a>
    <a href="#">Contact <span>Vireo</span></a>
  </nav>
</header>

<div class="abs tagline-small">We turn aspiring musicians into</div>
<div class="abs tagline-big">SuperStars!</div>

<div class="abs signup-bg"></div>
<section class="abs signup">
  <h2><span class="l1">Get found and</span><span class="l2">Become a star!</span></h2>
  <div class="field" style="left:46px;top:137px;width:305px;height:29px">First name</div>
  <span class="req" style="left:355px;top:132px">*</span>
  <div class="field" style="left:371px;top:137px;width:304px;height:29px">Last name</div>
  <span class="req" style="left:679px;top:132px">*</span>
  <div class="field" style="left:46px;top:183px;width:139px;height:30px">Age</div>
  <div class="field" style="left:209px;top:183px;width:142px;height:30px">Zip Code</div>
  <div class="field" style="left:371px;top:183px;width:304px;height:30px">Email Address</div>
  <span class="req" style="left:679px;top:178px">*</span>
  <div class="field" style="left:46px;top:226px;width:305px;height:30px">Daytime Phone</div>
  <div class="field" style="left:371px;top:226px;width:304px;height:30px">Evening Phone</div>
  <div class="field" style="left:46px;top:267px;width:629px;height:76px">Comments</div>
  <div class="abs artist-photo" role="img" aria-label="Black and white photo of a young artist in sunglasses and a hooded jacket wearing headphones"></div>
  <div class="abs submit">Submit</div>
</section>
<p class="abs form-note">After submitting, you will have the opportunity to upload demos of your music (optional) and provide other pertinent information about yourself, band, or group.</p>

<section class="abs welcome" role="img" aria-label="Background photo of a guitarist on a dim concert stage">
  <h1>Welcome <span>to Vireo</span></h1>
  <div class="copy">
    <p>Lorem ipsum dolor sit amet, consectetur adipiscing elit. Sed adipiscing sit amet sem sit amet viverra. Cras porta justo risus, quis sodales diam placerat vitae. Quisque eget dui orci. Cras aliquet, odio quis gravida fermentum, nibh lorem vulputate nunc, ut condimentum mauris ipsum non ipsum. Duis eleifend mauris nibh, ac hendrerit nisi bibendum dignissim. Nullam blandit urna vulputate nisl dignissim, vel tempus ante porttitor. Sed sed mi ac eros viverra rhoncus. Sed tempor sodales libero sit amet convallis.</p>
    <p>Morbi ac lectus lectus. Proin vitae facilisis enim. Suspendisse a fermentum magna. Curabitur accumsan ac magna ac vehicula. Sed sollicitudin, magna sed commodo pretium, arcu nunc tincidunt sem, quis laoreet felis eros et arcu. Maecenas porta tempus vulputate. Sed iaculis orci adipiscing lectus molestie dapibus. In vehicula, libero sit amet dapibus luctus, felis massa tincidunt eros, sodales fringilla lorem sem nec diam.</p>
  </div>
</section>

<div class="abs quote-rule"></div>
<div class="abs quote-badge"></div>
<div class="abs quote-mark">&ldquo;</div>
<blockquote class="abs quote-text">" Lorem ipsum dolor sit amet, consectetur adipiscing elit. In imperdiet diam augue,<br>vitae lacinia leo lacinia sit amet. Nulla facilisi. Cras cursus sed odio a mollis"</blockquote>
<p class="abs quote-author">Marcus Hale<span>producers</span></p>
<div class="abs dot on" style="left:567px;top:1595px"></div>
<div class="abs dot" style="left:585px;top:1595px"></div>
<div class="abs dot" style="left:603px;top:1595px"></div>

<div class="abs cream-strip"></div>
<section class="abs schedule">
  <h2><span class="l1">Concert</span><span class="l2">schedule</span></h2>
  <div class="abs next-bar">Next concert</div>
  <svg class="abs cal-icon" width="38" height="36" viewBox="0 0 38 36">
    <rect x="1" y="5" width="36" height="30" fill="none" stroke="#fff" stroke-width="2"/>
    <rect x="1" y="5" width="36" height="7" fill="#fff"/>
    <rect x="8" y="1" width="3" height="8" fill="#fff"/><rect x="27" y="1" width="3" height="8" fill="#fff"/>
    <g fill="#fff"><rect x="5" y="15" width="5" height="4"/><rect x="12" y="15" width="5" height="4"/><rect x="19" y="15" width="5" height="4"/><rect x="26" y="15" width="5" height="4"/><rect x="5" y="22" width="5" height="4"/><rect x="12" y="22" width="5" height="4"/><rect x="19" y="22" width="5" height="4"/><rect x="26" y="22" width="5" height="4"/><rect x="5" y="29" width="5" height="3"/><rect x="12" y="29" width="5" height="3"/></g>
  </svg>
  <div class="abs dot on" style="left:175px;top:217px"></div>
  <div class="abs dot" style="left:192px;top:217px"></div>
  <div class="abs dot" style="left:209px;top:217px"></div>
  <div class="abs gig" style="top:244px"><p class="date">2 November 2013</p><p class="venue">Harbor Arena - 2400 W Meridian Ave, Los Angeles, CA, US</p></div>
  <div class="abs gig-rule" style="top:343px"></div>
  <div class="abs gig" style="top:366px"><p class="date">10 November 2013</p><p class="venue">Harbor Arena - 2400 W Meridian Ave, Los Angeles, CA, US</p></div>
</section>
<div class="abs map" role="img" aria-label="Map of the south-western United States showing concert locations"></div>
<div class="abs map-pin" style="left:708px;top:1773px">10<br>Nov<br><span style="font-size:8px">2013</span></div>
<div class="abs map-pin" style="left:598px;top:1865px">2<br>Nov<br><span style="font-size:8px">2013</span></div>

<footer class="abs site-footer">
  <div class="abs footer-brand"><span class="name">VIREO</span><span class="sub">Music Productions</span></div>
  <p class="abs copyright">Copyright 2013 © Music Producers. Power by Brightframe</p>
  <p class="abs footer-links"><a href="#">Privacy Policy</a> | <a href="#">Terms and Conditions</a> | <a href="#">Site Map</a> | <a href="#">Feedback</a> | <a href="#">Report Bug</a> | <a href="#">Contact Us</a></p>
</footer>

</body>
</html>
```